High Tech Real Estate Startup needs a business card

We are developing an innovative real estate marketing product based around advanced search and virtual reality.

We talk to people, we need business cards.

Target Market(s)

The target market is technology professionals and realtors.

Contact Information for Business Card

The information to be included will include

Name
Title
Phone Number
E-mail Address
www.zelquin.com

It should use simple iconography for each one of those fields.

Font styles to use
Other font styles liked:
• Co, Jubilat, Avenir

Colors

Designer to choose colors to be used in the design.

Requirements
Must have
• Clean aesthetic,
• Good use of negative space.
• It should use our company logo, shown in the attached file. It is able to use the negative of that logo (coloured font and white background) and I have attached other acceptable accent colours in a swatch file.
Should not have
• Should not be too busy
• No extraneous text (slogans, tag lines etc)

```html
<!DOCTYPE html>
<html lang="en">
<head>
<meta charset="utf-8">
<title>Zelquin Business Card</title>
<link rel="stylesheet" href="https://fonts.googleapis.com/css2?family=Mulish:wght@300;400;500&display=swap">
<style>
  :root {
    --teal: #0bb4b8;
    --white: #ffffff;
    --ink: #3f4c56;
    --backdrop: #e9e4da;
  }
  html, body {
    margin: 0;
    padding: 0;
    width: 1200px;
    height: 1000px;
    overflow: hidden;
    background: var(--backdrop);
    font-family: "Mulish", sans-serif;
  }
  .canvas {
    position: relative;
    width: 1200px;
    height: 1000px;
  }
  .card {
    position: absolute;
    left: 270px;
    width: 658px;
    height: 375px;
    background: var(--white);
    overflow: hidden;
  }
  .card-front { top: 78px; }
  .card-back { top: 534px; }

  .front-wordmark {
    position: absolute;
    left: 0;
    right: 0;
    top: 140px;
    text-align: center;
    font-size: 76px;
    font-weight: 500;
    letter-spacing: 2px;
    line-height: 1;
    color: var(--teal);
  }

  .back-wave {
    position: absolute;
    inset: 0;
    width: 658px;
    height: 375px;
  }
  .person-name {
    position: absolute;
    left: 47px;
    top: 86px;
    margin: 0;
    font-size: 32px;
    font-weight: 400;
    color: var(--white);
    line-height: 1;
  }
  .person-title {
    position: absolute;
    left: 48px;
    top: 130px;
    margin: 0;
    font-size: 19px;
    font-weight: 400;
    color: var(--white);
    line-height: 1;
  }
  .back-wordmark {
    position: absolute;
    right: 40px;
    top: 190px;
    font-size: 54px;
    font-weight: 500;
    letter-spacing: 1px;
    line-height: 1;
    color: var(--white);
  }
  .contact-list {
    position: absolute;
    left: 46px;
    top: 246px;
    margin: 0;
    padding: 0;
    list-style: none;
  }
  .contact-item {
    display: flex;
    align-items: center;
    height: 36px;
    font-size: 22px;
    color: var(--ink);
  }
  .contact-icon {
    width: 18px;
    height: 18px;
    margin-right: 22px;
    fill: var(--ink);
  }
  .website {
    position: absolute;
    right: 74px;
    top: 320px;
    font-size: 20px;
    color: var(--teal);
    line-height: 1;
  }
</style>
</head>
<body>
<main class="canvas">
  <section class="card card-front" aria-label="Card front">
    <div class="front-wordmark">ZELQUIN</div>
  </section>

  <section class="card card-back" aria-label="Card back">
    <svg class="back-wave" viewBox="0 0 658 375" aria-hidden="true">
      <path fill="var(--teal)" d="M0,0 H658 V275 C600,296 540,306 470,300 C330,286 150,200 0,242 Z"/>
      <path fill="none" stroke="var(--white)" stroke-width="4" d="M0,212 C140,165 330,230 460,270 C520,286 570,292 605,290"/>
    </svg>
    <h1 class="person-name">Name of Person</h1>
    <p class="person-title">Title of Person</p>
    <div class="back-wordmark">ZELQUIN</div>
    <ul class="contact-list">
      <li class="contact-item">
        <svg class="contact-icon" viewBox="0 0 24 24" aria-hidden="true">
          <path d="M6.6 10.8c1.4 2.8 3.8 5.1 6.6 6.6l2.2-2.2c.3-.3.7-.4 1-.2 1.1.4 2.3.6 3.6.6.6 0 1 .4 1 1V20c0 .6-.4 1-1 1C10.6 21 3 13.4 3 4c0-.6.4-1 1-1h3.5c.6 0 1 .4 1 1 0 1.3.2 2.5.6 3.6.1.3 0 .7-.2 1l-2.3 2.2z"/>
        </svg>
        <span>+123 456 7890</span>
      </li>
      <li class="contact-item">
        <svg class="contact-icon" viewBox="0 0 24 24" aria-hidden="true">
          <path d="M2 6h20v1.2l-10 6.3L2 7.2z M2 9.3l10 6.3 10-6.3V19H2z"/>
        </svg>
        <span>E-mail Address</span>
      </li>
    </ul>
    <div class="website">www.zelquin.com</div>
  </section>
</main>
</body>
</html>
```